VELKO Website Redesign in Wix

Task:
Create a new design for all pages of the VELKO technology website in Wix. Specifications are:
Color palette preferences: black, white, gray, purple, blue. See VELKO Ref Doc provided.
Please refer to the VELKO_ref doc for a sample of the desired color palette
Typesetting must be in Montserrat
Brand will be that of a Marketing Technology company
Looking for vibrant, highly engaging images and organized, digestible flow. Open to suggestions
Required format is Wix.
VELKO logo does NOT need to be redesigned. Please use the files provided for the VELKO logo.
Look and feel
Each slider illustrates characteristics of the customer's brand and the style your logo design should communicate.

```html
<!DOCTYPE html>
<html lang="en">
<head>
<meta charset="utf-8">
<title>VELKO — Self-service content delivery</title>
<link href="https://fonts.googleapis.com/css2?family=Montserrat:wght@400;500;600;700;800&display=swap" rel="stylesheet">
<style>
:root{
  --ink:#111;
  --white:#fff;
  --blue:#1b7bc4;
  --navy-purple:#2a0f3e;
  --deep-purple:#2b1760;
  --lavender:#e3ccef;
  --lilac:#dccaea;
  --ice:#d6e7ef;
  --grey-text:#555;
  --black:#000;
  --accent:#3a1fa8;
}
*{box-sizing:border-box;margin:0;padding:0}
html,body{width:1200px;height:4027px;overflow:hidden}
body{font-family:'Montserrat',sans-serif;color:var(--ink);background:var(--white);position:relative}
.abs{position:absolute}
/* header */
.site-header{height:98px;width:1200px;position:relative;background:var(--white);border-bottom:1px solid #ddd}
.brand{left:144px;top:22px;font-size:54px;font-weight:600;letter-spacing:12px;color:var(--black);line-height:1}
.brand sup{font-size:8px;letter-spacing:0;vertical-align:top}
.main-nav{left:457px;top:40px;display:flex;gap:20px;font-size:12px;font-weight:500}
.main-nav a{color:var(--ink);text-decoration:none}
.main-nav a.active{border-bottom:2px solid var(--accent);padding-bottom:4px}
.user-icon{left:1040px;top:39px}
/* hero */
.hero{top:98px;height:575px;width:1200px;background:linear-gradient(160deg,#3a2a6a 0%,#261551 45%,#1d0f45 100%)}
.hero-title{top:232px;width:1200px;text-align:center;color:var(--white);font-size:40px;font-weight:700;line-height:50px}
.btn{display:inline-block;background:var(--blue);color:var(--white);font-weight:700;text-align:center;text-decoration:none}
.hero .btn{left:507px;top:412px;width:185px;height:53px;line-height:53px;font-size:16px}
.partners-label{top:527px;width:1200px;text-align:center;color:var(--white);font-size:14px;font-weight:500}
/* partners */
.partners{top:673px;height:88px;width:1200px;background:var(--black);color:var(--white);font-weight:600}
.partner{top:0;height:88px;display:flex;align-items:center;gap:8px;font-size:18px}
.partner .dot{width:22px;height:22px;border-radius:50%;border:2px solid #fff}
/* about */
.about{top:761px;height:609px;width:1200px;background:var(--white)}
.rule{width:40px;height:3px;background:var(--deep-purple)}
.sec-title{font-size:46px;font-weight:800;line-height:1.15;color:var(--black)}
.about .rule{left:144px;top:93px}
.about .sec-title{left:144px;top:110px}
.person-name{left:144px;top:186px;font-size:22px;font-weight:700;color:var(--blue)}
.person-role{left:144px;top:218px;font-size:15px;color:var(--blue)}
.about-text{left:144px;top:243px;width:525px;font-size:13px;line-height:27px;color:var(--grey-text)}
.about .btn{left:144px;top:472px;width:186px;height:54px;line-height:54px;font-size:17px}
.portrait{left:743px;top:0;width:457px;height:609px;background:linear-gradient(180deg,#e6d2f0,#d8c1e6)}
/* how */
.how{top:1370px;height:733px;width:1200px;background:linear-gradient(180deg,#dbeaf1 0%,#c9dde8 100%)}
.how .rule{left:144px;top:78px}
.how .sec-title{left:142px;top:96px}
.card{background:var(--white);text-align:center}
.how .card{top:196px;width:289px;height:339px;padding:44px 30px 0}
.card h3{font-size:16px;font-weight:700;color:var(--black)}
.card p{font-size:13px;line-height:24px;color:var(--grey-text);margin-top:24px}
.btn-dark{display:inline-block;background:var(--navy-purple);color:var(--white);font-size:12px;font-weight:700}
.how .btn-dark{position:absolute;left:75px;top:254px;width:139px;height:39px;line-height:39px}
.how .view{left:514px;top:584px;width:186px;height:53px;line-height:53px;font-size:17px}
/* platform */
.platform{top:2103px;height:656px;width:1200px;background:var(--white)}
.platform-photo{left:0;top:0;width:453px;height:656px;background:linear-gradient(135deg,#8a8a8a,#3c3c3c 60%,#6b6b6b)}
.platform .rule{left:514px;top:70px}
.platform .sec-title{left:514px;top:88px}
.platform-text{left:514px;top:226px;width:540px;font-size:16px;line-height:27px;color:#444}
.platform-text p+p{margin-top:27px}
.platform .btn{left:514px;top:453px;width:186px;height:53px;line-height:53px;font-size:17px}
/* applications */
.applications{top:2759px;height:733px;width:1200px;background:linear-gradient(180deg,#e2d1ee,#d6c2e6)}
.applications .rule{left:144px;top:80px}
.applications .sec-title{left:142px;top:97px}
.app-card{top:197px;height:339px;width:439px;padding:44px 44px 0;background:var(--white);text-align:left}
.app-card h3{font-size:16px;font-weight:700;line-height:27px}
.app-card p{font-size:13px;line-height:24px;color:var(--grey-text);margin-top:20px}
.app-card .btn-dark{position:absolute;left:44px;bottom:48px;width:139px;height:39px;line-height:39px;text-align:center}
.applications .view{left:514px;top:583px;width:186px;height:53px;line-height:53px;font-size:17px}
/* footer */
.site-footer{top:3492px;height:535px;width:1200px;background:var(--black);color:var(--white)}
.contact-title{left:187px;top:77px;font-size:21px;font-weight:700}
.contact-list{left:187px;top:122px;font-size:16px;line-height:48px}
.socials{left:187px;top:305px;display:flex;gap:10px}
.socials span{width:41px;height:41px;border-radius:50%;border:2px solid #fff}
.contact-form{left:631px;top:72px;width:381px}
.field{height:42px;border:1px solid #bbb;background:var(--white);color:#333;font-size:13px;padding:12px 14px;margin-bottom:14px}
.field.msg{height:76px}
.submit{margin-left:233px;margin-top:0;width:148px;height:43px;line-height:43px;background:var(--blue);color:var(--white);font-size:13px;font-weight:700;text-align:center}
.legal{left:187px;top:454px;font-size:15px}
.chat{left:1112px;top:402px;width:52px;height:52px;border-radius:14px;background:#5b18e0}
</style>
</head>
<body>

<header class="site-header">
  <div class="brand abs">VELKO<sup>TM</sup></div>
  <nav class="main-nav abs">
    <a class="active" href="#">HOME</a><a href="#">HOW IT WORKS</a><a href="#">VELKO APPLICATIONS</a><a href="#">COMPANY</a><a href="#">CONTACT US</a><a href="#">MORE</a>
  </nav>
  <svg class="user-icon abs" width="16" height="17" viewBox="0 0 16 17"><circle cx="8" cy="5" r="4.3" fill="#3a1fa8"/><path d="M0 17c0-5 3.5-7 8-7s8 2 8 7z" fill="#3a1fa8"/></svg>
</header>

<section class="hero abs" role="img" aria-label="Photo of a man in glasses looking at a screen, tinted deep purple">
  <h1 class="hero-title abs">Increase and perfect your connection<br>with consumers using VELKO™’s patented<br>self-service content delivery technology</h1>
  <a class="btn abs" href="#">GET STARTED</a>
  <p class="partners-label abs">OUR CUSTOMERS AND PARTNERS</p>
</section>

<section class="partners abs">
  <div class="partner abs" style="left:168px"><span class="dot"></span>Northvale</div>
  <div class="partner abs" style="left:402px"><span class="dot"></span>GREYFIELD LTD</div>
  <div class="partner abs" style="left:628px">Harbor Arts Week</div>
  <div class="partner abs" style="left:838px;letter-spacing:3px;font-weight:500">ORLEN&amp;CASTELL</div>
</section>

<section class="about abs">
  <div class="rule abs"></div>
  <h2 class="sec-title abs">ABOUT ME</h2>
  <p class="person-name abs">Marcus Lindqvist</p>
  <p class="person-role abs">Co-Founder and Chief Technology Officer</p>
  <p class="about-text abs">Marcus Lindqvist is the co-founder and CTO of VELKO™ Technologies. He is an expert and highly respected tactical leader in the data, financial and technology sectors. With more than two decades of innovative leadership experience, he has led numerous companies to success and acquisition, such as Brightwren for more than $44.5 million and TAGLOOP for $5.3 million. Mr. Lindqvist was also involved in the acquisition and consolidation of internet radio operations at Kestrel Technologies, which he founded in 2010.</p>
  <a class="btn abs" href="#">READ MORE</a>
  <div class="portrait abs" role="img" aria-label="Portrait of the co-founder in a grey suit on a lavender background"></div>
</section>

<section class="how abs" role="img" aria-label="Pale blue photo backdrop of hands using a phone over a city skyline">
  <div class="rule abs"></div>
  <h2 class="sec-title abs">HOW IT WORKS</h2>
  <div class="card abs" style="left:144px"><h3>CONTENT CREATION</h3><p>Self service content creation allows businesses to easily create and execute any campaign. VELKO packets can be delivered in real time or time released through television.</p><a class="btn-dark" href="#">READ MORE</a></div>
  <div class="card abs" style="left:456px"><h3>COMPLIANCE &amp; SECURITY</h3><p>Multi-layered solutions meeting identity verification, privacy and data sovereignty regulations. Cyber security provided by Greyfield Ltd</p><a class="btn-dark" href="#">READ MORE</a></div>
  <div class="card abs" style="left:767px"><h3>CONSUMER APP</h3><p>Consumers have the opportunity to knowingly Opt in to interact with content.<br>Non-invasive VELKO technology providing two way communication.</p><a class="btn-dark" href="#">READ MORE</a></div>
  <a class="btn view abs" href="#">VIEW MORE</a>
</section>

<section class="platform abs">
  <div class="platform-photo abs" role="img" aria-label="Black and white photo of two young people sitting on steps using their phones"></div>
  <div class="rule abs"></div>
  <h2 class="sec-title abs">OUR REVOLUTIONARY<br>PLATFORM</h2>
  <div class="platform-text abs">
    <p>Whether you’re marketing software, selling a product, or looking to close a deal – find out your target market and quickly modify your campaigns to reach consumers silently and securely.</p>
    <p>Our platform goes far beyond basic ad optimization to deliver individualized content that immediately increases engagement over any communication medium with embedded tones.</p>
  </div>
  <a class="btn abs" href="#">READ MORE</a>
</section>

<section class="applications abs" role="img" aria-label="Lilac-tinted photo backdrop of a person wearing headphones with a soft bar graphic">
  <div class="rule abs"></div>
  <h2 class="sec-title abs">APPLICATIONS</h2>
  <div class="app-card abs" style="left:144px"><h3>ADVERTISING/MARKETING<br>/EXHIBITIONS</h3><p>Transformative technology conveniently and seamlessly offers 2 way communication with consumers.Embed VELKO packets into media content that provides purchase suggestions and information to consumers phones.</p><a class="btn-dark" href="#">READ MORE</a></div>
  <div class="app-card abs" style="left:617px;padding-left:50px"><h3>DIGITAL RIGHTS MANAGEMENT</h3><p>Next-gen digital watermarking and digital rights management solution for Film and Music Industry.</p><p>Embed VELKO packets to track and identify the utilization of copyrighted media without degrading sound quality.</p><a class="btn-dark" href="#" style="left:50px">READ MORE</a></div>
  <a class="btn view abs" href="#">VIEW MORE</a>
</section>

<footer class="site-footer abs">
  <h2 class="contact-title abs">CONTACT</h2>
  <div class="contact-list abs"><p>Phone</p><p>1-800-555-0142</p><p>Email</p><p>hello@velkotech.example</p></div>
  <div class="socials abs"><span></span><span></span><span></span><span></span></div>
  <form class="contact-form abs">
    <div class="field">Enter Name</div>
    <div class="field">Enter Email</div>
    <div class="field">Enter Subject</div>
    <div class="field msg">Message</div>
    <div class="submit">SUBMIT</div>
  </form>
  <p class="legal abs">© 2022 velkotech All Rights Reserved &nbsp;| Privacy Policy &nbsp;| &nbsp;Terms and use</p>
  <div class="chat abs">
    <svg width="52" height="52" viewBox="0 0 52 52"><circle cx="26" cy="25" r="11" fill="#fff"/><path d="M17 33l-2 5 6-3z" fill="#fff"/><circle cx="22" cy="25" r="1.6" fill="#5b18e0"/><circle cx="26" cy="25" r="1.6" fill="#5b18e0"/><circle cx="30" cy="25" r="1.6" fill="#5b18e0"/></svg>
  </div>
</footer>

</body>
</html>
```